Corvane Card

The logo is the Spanish flag colors I want a vibrant eye catching design with the yellow / red colors over either Navy or white background or black even ,
Would like a 2D feel to the logo with another lighter color logo under it look ,

Contact Information for Business Card

Corvane Flooring
Teodor Vashkin
Main Number
Cell Number
Fax Number

Website on the side of the card somewhere

Font styles to use
Sans Serif

Colors
ec1f27
ffc214

Requirements
Must have
• 2 logos feel one is bolder and the other one underneath very light

```html
<!DOCTYPE html>
<html lang="en">
<head>
<meta charset="utf-8">
<title>Corvane Flooring – Business Card</title>
<link href="https://fonts.googleapis.com/css2?family=Ubuntu:wght@400;500;700&display=swap" rel="stylesheet">
<style>
  :root {
    --brand-red: #ec1f27;
    --brand-yellow: #ffc214;
    --card-black: #050505;
    --card-white: #ffffff;
    --text-light: #f2f2f2;
    --stage: #e6e3de;
  }
  * { margin: 0; padding: 0; box-sizing: border-box; }
  html, body { width: 1200px; height: 675px; overflow: hidden; }
  body {
    background: var(--stage);
    font-family: "Ubuntu", sans-serif;
    position: relative;
  }
  .card {
    position: absolute;
    top: 183px;
    width: 540px;
    height: 309px;
    overflow: hidden;
    box-shadow: 0 6px 18px rgba(0,0,0,0.18);
  }
  .card--front { left: 45px; background: var(--card-black); color: var(--text-light); }
  .card--back { left: 615px; background: var(--card-white); }
  .corner-accent { position: absolute; inset: 0; width: 100%; height: 100%; }

  .wordmark { display: flex; align-items: center; gap: 8px; }
  .wordmark__square { width: 14px; height: 14px; background: var(--brand-red); flex: none; }
  .wordmark__name {
    font-weight: 700; color: var(--brand-yellow);
    letter-spacing: 1.5px; text-transform: uppercase; white-space: nowrap;
  }

  .card--front .wordmark { position: absolute; left: 40px; top: 34px; }
  .card--front .wordmark__name { font-size: 17px; }

  .holder { position: absolute; left: 40px; top: 104px; }
  .holder__name { color: var(--brand-red); font-weight: 700; font-size: 15px; text-transform: uppercase; letter-spacing: 0.3px; }
  .holder__title { font-size: 11px; margin-top: 2px; }

  .contacts { position: absolute; left: 40px; top: 150px; list-style: none; font-size: 13px; line-height: 19px; }
  .contacts li { display: flex; align-items: center; gap: 8px; }
  .contacts svg { width: 12px; height: 12px; flex: none; }

  .address {
    position: absolute; left: 220px; top: 232px;
    font-size: 13px; line-height: 18px; font-style: normal; white-space: nowrap;
  }

  .card--back .wordmark {
    position: absolute; left: 0; right: 0; top: 150px; justify-content: center;
  }
  .card--back .wordmark__name { font-size: 24px; }
  .website {
    position: absolute; left: 0; right: 0; top: 200px; text-align: center;
    color: var(--brand-red); font-size: 15px; letter-spacing: 1.8px;
  }
</style>
</head>
<body>
  <section class="card card--front">
    <svg class="corner-accent" viewBox="0 0 540 309" aria-hidden="true">
      <polygon points="400,309 540,120 540,309" fill="var(--brand-red)"/>
      <polygon points="455,309 540,195 540,309" fill="var(--brand-yellow)"/>
    </svg>
    <div class="wordmark">
      <span class="wordmark__square"></span>
      <span class="wordmark__name">Corvane Flooring</span>
    </div>
    <div class="holder">
      <p class="holder__name">Teodor Vashkin</p>
      <p class="holder__title">Managing Director</p>
    </div>
    <ul class="contacts">
      <li>
        <svg viewBox="0 0 12 12"><rect width="12" height="12" fill="var(--brand-red)"/><path d="M3.5 2.5l1.5 1.2-.7 1.1c.5 1 1.3 1.8 2.3 2.3l1.1-.7 1.2 1.5-.9.9C5.5 8.6 3.4 6.5 2.6 3.4z" fill="#fff"/></svg>
        <span>0140 482 615</span>
      </li>
      <li>
        <svg viewBox="0 0 12 12"><rect width="12" height="12" fill="var(--brand-red)"/><rect x="3" y="2.5" width="6" height="7" rx="1" fill="#fff"/></svg>
        <span>2468 305 917</span>
      </li>
      <li>
        <svg viewBox="0 0 12 12"><rect width="12" height="12" fill="var(--brand-red)"/><rect x="2.5" y="3.5" width="7" height="5" fill="#fff"/><path d="M2.5 3.5L6 6.5 9.5 3.5" stroke="var(--brand-red)" fill="none" stroke-width="0.8"/></svg>
        <span>info@corvaneflooring.com</span>
      </li>
    </ul>
    <address class="address">
      Suite 214 Orrin Lane, Calder,<br>Zip 4172, Norvale
    </address>
  </section>

  <section class="card card--back">
    <svg class="corner-accent" viewBox="0 0 540 309" aria-hidden="true">
      <polygon points="0,0 210,0 0,260" fill="var(--brand-red)"/>
      <polygon points="0,0 120,0 0,150" fill="var(--brand-yellow)"/>
    </svg>
    <div class="wordmark">
      <span class="wordmark__square"></span>
      <span class="wordmark__name">Corvane Flooring</span>
    </div>
    <p class="website">www.corvaneflooring.com</p>
  </section>
</body>
</html>
```